International professional tennis coach needs a book cover design

This is my 2nd published book, the first one was a #1 on the best seller. I'm looking for a world class book cover design for this new book. The name of my first book was 5 Baseline Habits to Unlock Your Flow Rhythm, located on Bookvale.com

The title of the new book:

Title: The Craft of Rally Mastery
Subtitle: Developing a Strategic Advantage through Competitive Intelligence

I'm uploading our new CRAFT OF RALLY logo that I'd like for you to use as the centerpiece of the book design along with a 21st century design feel that incorporates what the book topic is below::

--> This book is about building competitive intelligence by using tennis data analytics to develop and expand a player's strategic advantage for match play. <--

The colors we would like to use are Blue, Yellow, and Green. These shades of these colors should be bold! (You will see the bold color examples of blues, yellows, and greens that I'm talking about in the logos that are attached here, especially the colors for my Racket GridDrill App logo.

I will upload the Racket GridDrill logo which should go somewhere on the back cover design (small size maybe in the bottom corner).

This book is revolutionary to the standard way of teaching tennis, it is based on a decade of recording and gathering tennis data analytics and then we created on-court practice games to develop better decision making in players for the competitive edge.

My websites are www.elevatedrillzone.com and www.craftofrallymastery.com

```html
<!DOCTYPE html>
<html lang="en">
<head>
<meta charset="utf-8">
<title>The Craft of Rally Mastery – Book Jacket</title>
<link rel="stylesheet" href="https://fonts.googleapis.com/css2?family=Libre+Baskerville:wght@400;700&family=Parisienne&family=Oswald:wght@400;500&family=Lato:wght@400;700&display=swap">
<style>
  :root {
    --green: #1f7a2b;
    --green-dark: #17661f;
    --flap-green: #2a7d2e;
    --blue: #3d6fb6;
    --yellow: #e3ad2b;
    --paper: #f4f4f2;
    --ink: #3b3b3b;
    --muted: #6a6a6a;
    --backdrop: #e9e7e1;
    --photo-tone: #8f9a8c;
  }
  * { box-sizing: border-box; margin: 0; padding: 0; }
  html, body {
    width: 1200px; height: 900px; overflow: hidden;
    background: var(--backdrop);
  }
  .jacket {
    position: absolute; left: 25px; top: 185px;
    width: 1150px; height: 530px;
    display: flex;
    box-shadow: 0 6px 18px rgba(0,0,0,.18);
  }
  .flap {
    width: 180px; height: 100%;
    background: var(--flap-green);
    color: #e8f2e6;
    font: 400 6.4px/1.45 "Lato", sans-serif;
    text-align: justify;
  }
  .flap--left { padding: 160px 20px 0 20px; }
  .flap--right { padding: 160px 20px 0 30px; }
  .flap p + p { margin-top: 4px; }

  .panel { background: var(--paper); height: 100%; position: relative; }
  .back { width: 375px; padding: 22px 24px 0 22px; color: var(--ink); }
  .spine { width: 40px; border-left: 1px solid #ddd; border-right: 1px solid #ddd; }
  .front { width: 375px; text-align: center; }

  .script { font-family: "Parisienne", cursive; color: var(--green); font-weight: 400; }

  .back-heading { text-align: center; white-space: nowrap; margin-bottom: 14px; }
  .back-heading .script { font-size: 15px; }
  .back-heading .title-small {
    font: 700 20px/1 "Libre Baskerville", serif; color: var(--green);
  }
  .blurb { font: 400 6.7px/1.35 "Lato", sans-serif; text-align: justify; }
  .blurb p + p { margin-top: 3px; }

  .author-name {
    font: 700 15px/1 "Libre Baskerville", serif; color: var(--green);
    text-align: center; margin: 14px 0 9px;
  }
  .author { display: flex; gap: 8px; }
  .author-photo {
    flex: 0 0 72px; height: 72px;
    background: linear-gradient(160deg, #a9b3a5, var(--photo-tone) 60%, #5f6b5c);
  }
  .author-bio { font: 400 6.4px/1.35 "Lato", sans-serif; text-align: justify; }

  .app-mark {
    position: absolute; left: 24px; bottom: 22px;
    display: flex; align-items: center; gap: 5px;
    font: 700 7px/1 "Lato", sans-serif; color: var(--blue);
  }
  .app-mark .dot { width: 12px; height: 12px; border-radius: 50%; background: var(--green); }

  .spine-text {
    position: absolute; left: 50%; top: 12px;
    transform: translateX(-50%);
    writing-mode: vertical-rl;
    display: flex; align-items: center; gap: 10px;
    white-space: nowrap;
  }
  .spine-text .script { font-size: 13px; }
  .spine-title { font: 700 15px/1 "Libre Baskerville", serif; color: var(--green); }
  .spine-mark { width: 14px; height: 14px; border-radius: 50%; background: var(--yellow); margin: 14px 0; }
  .spine-authors { font: 500 13px/1 "Oswald", sans-serif; color: var(--green); }

  .front-script { font-size: 40px; line-height: 1; margin-top: 26px; }
  .front-title {
    font: 700 58px/0.98 "Libre Baskerville", serif;
    color: var(--green); letter-spacing: -1px; margin-top: 2px;
  }
  .series-mark {
    margin: 52px auto 0; display: inline-flex; align-items: center; gap: 10px;
    font: 500 24px/1 "Oswald", sans-serif; color: var(--blue); letter-spacing: 1px;
  }
  .series-mark .dot { width: 26px; height: 26px; border-radius: 50%; background: var(--yellow); }
  .rule { width: 240px; height: 1px; background: #cfd6cc; margin: 58px auto 12px; }
  .subtitle { font: 400 14px/1.2 "Libre Baskerville", serif; color: var(--muted); }
  .front-authors {
    position: absolute; left: 0; right: 0; bottom: 26px;
    font: 500 20px/1 "Oswald", sans-serif; color: var(--green);
  }
</style>
</head>
<body>
<main class="jacket">
  <section class="flap flap--left">
    <p>Every rally tells a story when the numbers are read with care. This book turns years of match tracking into clear patterns, simple court games and steady habits that help a player choose the right shot under pressure. Coaches, parents and juniors will find a shared language for growth, built on data and refined through practice.</p>
    <p>Inside you will learn how to map a point, spot an opponent's habits and build a plan that holds from the first serve to the final ball.</p>
  </section>

  <section class="panel back">
    <h2 class="back-heading"><span class="script">The Craft of</span> <span class="title-small">RALLY MASTERY</span></h2>
    <div class="blurb">
      <p>A practical guide on how to win more matches by becoming a more efficient and effective competitor.</p>
      <p>As a tennis player you have the ability to play better matches and win more of them. The Craft of Rally Mastery gives you a system to improve. We start with the individual game of the set itself. Our system examines your physical and mental progression, enabling you to upgrade your movement and performance from shot to shot and point to point. Our system seamlessly integrates the technical (physical) aspects with the tactical (mental/emotional) components, providing a comprehensive approach to elevate this performance. We aim to give you much more than how to hit great shots. Irrespective of your current skill level, we will provide you with a detailed strategic and tactical plan to enhance your performance, leading to improved results and increased success in your matches.</p>
      <p>The Craft of Rally Mastery emphasizes the importance of shifting focus from oneself to the opponent, encouraging players to analyze and understand their adversaries. By bringing the opponent back to the forefront of their thinking, the player creates the best possible context in which to improve as a competitor. In this book, we present a groundbreaking approach to tennis data analytics that seamlessly integrates match performance with practice sessions, and vice versa.</p>
    </div>

    <h3 class="author-name">CORWIN HALVARD</h3>
    <div class="author">
      <div class="author-photo" role="img" aria-label="Portrait photo of author Corwin Halvard"></div>
      <p class="author-bio">Corwin Halvard is regarded as one of the leading strategy and tactical coaches in the world today. He is the Creator of Racket GridDrill, the world's first Tennis Tracking App that maps and charts match play based on the rally length of a point. Corwin is a Best Selling Author of the book "5 Baseline Habits to Unlock Your Flow Rhythm" and the Co-Founder of The Craft of Rally Mastery promoting coach, player, and parent development. He is often sought after by coaches around the world to design the practice court in a way that revolutionizes a player's mindset to successfully negotiate the pressures of competitive match play.</p>
    </div>

    <h3 class="author-name">MASON PELL</h3>
    <div class="author">
      <div class="author-photo" role="img" aria-label="Portrait photo of author Mason Pell"></div>
      <p class="author-bio">Mason Pell is a writer and tennis coach. He is a Co-Founder at The Craft of Rally Mastery and has been working to create a theoretical framework for tennis players of all levels to improve. Mason studies the forces that act on the player during a tennis match (both internal and external) and works with players to meet the challenge these forces represent. He runs online and on court programs designed specifically to improve a player's Competitive Intelligence.</p>
    </div>

    <div class="app-mark"><span class="dot"></span>Racket GridDrill</div>
  </section>

  <section class="panel spine">
    <div class="spine-text">
      <span class="script">The Craft of</span>
      <span class="spine-title">RALLY MASTERY</span>
      <span class="spine-mark"></span>
      <span class="spine-authors">CORWIN HALVARD &amp; MASON PELL</span>
    </div>
  </section>

  <section class="panel front">
    <p class="script front-script">The Craft of</p>
    <h1 class="front-title">RALLY<br>MASTERY</h1>
    <div class="series-mark"><span class="dot"></span>CRAFT OF RALLY</div>
    <div class="rule"></div>
    <p class="subtitle">Developing a Strategic Advantage<br>through Competitive Intelligence</p>
    <p class="front-authors">CORWIN HALVARD &amp; MASON PELL</p>
  </section>

  <section class="flap flap--right">
    <p>Praise for the method: Players who train with these court games report calmer decisions, sharper patterns and more wins in tight sets. The approach blends honest statistics with simple drills, so progress is easy to measure week after week. It works for club players, college teams and touring pros alike, and it keeps the focus on smart choices rather than raw power.</p>
  </section>
</main>
</body>
</html>
```